Im want a website LIKE VRX's and FleetHollow.com's with product payment options like Trenzo's

I need a website LIKE VRX with a header made EXACTLY LIKE THAT OF FLEETHOLLOWS .

The front page photo should be like that of FLEETHOLLOW's webpage as well.

The name of the website will be called "M.K. (Caldera Key)".

We will be targeting ALL MARKETS in a small town in central Panama and charging businesses "listing fees" like a phone book does but also providing informational blogs, news, and other interesting activities.

THIS IS A MULTI PAGE WEBSITE

THIS IS WHERE VRX's website meets Brivelle/FleetHollow.

Once the layout is built I will tweak and modify, add information, and upload items for sale.

Here is a list of specific categories that should be listed out above the front page header image/search bar

-- Home -- News -- Travel -- Activities -- Shop & Dine -- Store -- More... --

These categories should be spread across the bottom of the page in three sections:

WHATS SO GREAT ABOUT (Caldera Key),
HAND PICKED TOURS
ACTIVITIES etc.

Also lets use www.Trenzo.example 's
"HOT DESTINATIONS"
"BEAT THE BEST PRICES IN BOQUETE"
"OCTOBERS INSIDER PICKS"
"TOP DESTINATIONS"
and spread them in four sections side-by-side near the bottom of the page.

Overall I would like to see the finished product to be something LIKE VRX's and FleetHollows.

WE NEED ONLINE PAYMENT OPTIONS LIKE BRIVELLE'S WEBSITE HAS

This will be a desktop website but should be very mobile friendly as well.

-rodmund

P.S. Good luck!

If it isn't already too late to change the website name, the name of the website should be "Caldera Key". Added Friday, October 9, 2015

What do you guys think the budget should be to win this? Added Saturday, October 10, 2015

www.palmorra.example is the most amazing simple site. Whoever can make me a replica with my specifications will win immediately!!!! Added Sunday, October 18, 2015

OMG www.palmorra.example is the bomb!So simple and elegant. Whoever can make me an EXACT REPLICA OF WWW.PALMORRA.EXAMPLE as my site with the specifications mentioned in my brief will take home the $825.00 immediately! Good luck amigos! Added Sunday, October 18, 2015

Does anybody know how to add recurring monthly billing options on this website? Added Sunday, October 18, 2015

ALL MARKETS

Product

Coded - Design and coding required

5+ page

• Coinvey payment options.
• I must be able to add and remove photos/text and video from the HTML files in the page.
• Be creative my friends, and may the odds be forever in your favor!
• I added some photos of a good layout for our page below.

```html
<!DOCTYPE html>
<html lang="en">
<head>
<meta charset="utf-8">
<title>Caldera Key — Travel With Us</title>
<link href="https://fonts.googleapis.com/css2?family=Montserrat:wght@400;600;700&family=Open+Sans:wght@400;600;700&family=Dancing+Script:wght@600&display=swap" rel="stylesheet">
<style>
:root{
  --teal:#1fa89b;
  --teal-dark:#17877d;
  --ink:#2f343b;
  --ink-2:#3b4048;
  --text:#6d737a;
  --line:#e4e7ea;
  --paper:#ffffff;
  --soft:#f4f6f7;
  --gold:#f3b634;
  --red:#e4544a;
  --footer:#2b2f35;
}
*{box-sizing:border-box;margin:0;padding:0}
html,body{width:1200px;height:4376px;overflow:hidden}
body{font-family:"Open Sans",Arial,sans-serif;color:var(--text);background:var(--paper);font-size:13px;line-height:1.55}
h1,h2,h3,h4{font-family:"Montserrat",Arial,sans-serif;color:var(--ink);font-weight:700}
.wrap{width:1040px;margin:0 auto;position:relative}
.script{font-family:"Dancing Script",cursive;color:var(--text);font-size:18px;text-align:center;display:block}
.section-title{font-size:30px;text-align:center;letter-spacing:1px;margin-top:2px}
.btn{display:inline-block;background:var(--teal);color:#fff;font-family:"Montserrat",sans-serif;font-weight:700;font-size:11px;letter-spacing:1px;padding:9px 20px;border-radius:20px}
.btn-dark{background:var(--ink);border-radius:2px}
.arrow{position:absolute;width:34px;height:34px;background:var(--teal);display:flex;align-items:center;justify-content:center}
.stars{color:var(--gold);font-size:13px;letter-spacing:2px}

/* top bar */
.topbar{height:32px;background:#262a30;color:#aab0b6;font-size:11px}
.topbar .wrap{display:flex;justify-content:space-between;align-items:center;height:32px}
.topbar .social{display:flex;gap:8px}
.topbar .social span{width:12px;height:12px;border-radius:50%;background:#5c636b;display:block}

/* header */
.header{height:80px;background:var(--ink-2)}
.header .wrap{display:flex;justify-content:space-between;align-items:center;height:80px}
.brand{display:flex;align-items:center;gap:10px;font-family:"Montserrat",sans-serif;font-weight:700;font-size:24px;color:#fff}
.brand i{width:14px;height:14px;background:var(--teal);display:block}
.nav{display:flex;gap:30px;font-family:"Montserrat",sans-serif;font-weight:700;font-size:11px;letter-spacing:1px;color:#fff}
.nav a.active{color:var(--teal)}

/* hero */
.hero{height:528px;position:relative;background:linear-gradient(180deg,#3e8fc7 0%,#7fbde0 45%,#cfe3e6 62%,#b79a63 78%,#8a6d3e 100%)}
.hero h1{position:absolute;top:236px;left:0;right:0;text-align:center;color:#fff;font-size:46px;letter-spacing:3px;text-shadow:0 2px 6px rgba(0,0,0,.25)}
.hero .arrow.l{left:0;top:248px}.hero .arrow.r{right:0;top:248px}

/* why choose us */
.why{height:360px;padding-top:44px}
.why .wrap{display:flex;justify-content:space-between}
.why h2{font-size:26px;margin-bottom:26px}
.features{display:grid;grid-template-columns:repeat(3,230px);gap:36px 30px;width:760px}
.feature{display:flex;gap:14px}
.feature .ic{flex:0 0 40px;height:40px;border-radius:50%;background:var(--teal);display:flex;align-items:center;justify-content:center}
.feature h4{font-size:13px;margin-bottom:4px}
.feature p{font-size:11.5px;line-height:1.5}
.search{width:240px;background:var(--teal);padding:20px 18px;margin-top:-10px;height:290px}
.search h3{font-family:"Dancing Script",cursive;color:#fff;font-size:22px;text-align:center;font-weight:600}
.search small{display:block;color:#dff3f1;text-align:center;font-size:11px;margin-bottom:14px}
.search .field{background:#fff;height:32px;margin-bottom:10px;font-size:11px;color:#888;padding:7px 10px;display:flex;justify-content:space-between}
.search .btn{display:block;text-align:center;margin-top:6px}

/* popular tours */
.popular{height:720px;position:relative;background:linear-gradient(180deg,#f4f6f7 0%,#dfe8ee 18%,#9fb8ca 32%,#5e7d94 48%,#3b5060 62%,#6a6058 80%,#8b7e70 100%);padding-top:48px}
.popular .section-title{margin-bottom:34px}
.cards3{display:flex;justify-content:center;gap:30px}
.tour{width:290px;background:#fff;box-shadow:0 3px 10px rgba(0,0,0,.15);position:relative}
.tour .photo{height:190px;position:relative}
.ribbon{position:absolute;top:10px;right:10px;background:var(--teal);color:#fff;font-size:10px;font-weight:700;padding:3px 8px}
.price{position:absolute;right:0;bottom:0;background:var(--teal);color:#fff;font-family:"Montserrat",sans-serif;font-weight:700;font-size:16px;padding:6px 14px}
.price s{font-size:11px;opacity:.8;margin-right:6px}
.tour .body{padding:16px 18px 10px}
.tour h3{font-size:17px;margin-bottom:6px}
.tour p{font-size:11.5px;height:54px}
.tour .meta{border-top:1px solid var(--line);padding:9px 18px;font-size:11px;display:flex;justify-content:space-between}
.popular .arrow.l{left:80px;top:300px}.popular .arrow.r{right:80px;top:300px}

/* deals */
.deals{height:540px;padding-top:50px}
.deals .head{display:flex;justify-content:space-between;align-items:center}
.deals h2{font-size:26px;border-left:4px solid var(--teal);padding-left:12px}
.deals .sub{font-size:12px;margin:8px 0 28px 16px}
.cards4{display:flex;gap:20px}
.deal{width:245px;border:1px solid var(--line);background:#fff}
.deal .photo{height:150px;position:relative}
.deal .badge{position:absolute;top:10px;right:10px;width:52px;height:52px;border-radius:50%;background:var(--red);color:#fff;font-family:"Montserrat",sans-serif;font-weight:700;font-size:13px;display:flex;align-items:center;justify-content:center;flex-direction:column;line-height:1.1}
.deal .badge small{font-size:9px;font-weight:400}
.deal .body{padding:14px}
.deal h3{font-size:15px;margin-bottom:5px}
.deal p{font-size:11.5px;height:36px}
.deal .meta{border-top:1px solid var(--line);padding:8px 14px;font-size:11px;display:flex;justify-content:space-between}

/* hot destinations */
.hot{height:400px;padding-top:60px}
.hot .section-title{margin-bottom:36px}
.tiles{display:flex;gap:20px}
.tile{width:245px;height:160px;position:relative;display:flex;align-items:center;justify-content:center}
.tile span{color:#fff;font-family:"Montserrat",sans-serif;font-weight:700;font-size:20px;text-shadow:0 2px 4px rgba(0,0,0,.4)}

/* tour type */
.types{height:380px;position:relative;background:linear-gradient(180deg,#4a5a6c 0%,#2f3c4a 55%,#253039 100%);padding-top:50px}
.types .script{color:#cfd6dc}
.types .section-title{color:#fff;margin-bottom:40px}
.type-row{display:flex;justify-content:center;gap:56px}
.type{text-align:center;color:#fff;font-family:"Montserrat",sans-serif;font-weight:700;font-size:11px;letter-spacing:1px}
.type .ring{width:120px;height:120px;border:3px solid #fff;border-radius:50%;display:flex;align-items:center;justify-content:center;margin-bottom:12px}
.types .arrow.l{left:80px;top:200px}.types .arrow.r{right:80px;top:200px}

/* insider + reviews */
.insider{height:680px;padding-top:56px}
.insider .wrap{display:flex;justify-content:space-between}
.col-h{font-size:22px;text-align:center;margin-bottom:24px}
.pick{width:560px;position:relative}
.pick .photo{height:430px;background:linear-gradient(180deg,#e9b676 0%,#d98a4a 35%,#8c7c5d 65%,#4c5a3e 100%)}
.pick .caption{position:absolute;left:90px;right:90px;top:300px;background:#fff;padding:18px 22px;text-align:center;box-shadow:0 3px 10px rgba(0,0,0,.12)}
.pick .caption h3{font-size:18px;margin-bottom:8px}
.pick .caption p{font-size:11.5px;margin-bottom:12px}
.pick .arrow.l{left:0;top:390px}.pick .arrow.r{right:0;top:390px}
.side{width:420px}
.review{display:flex;gap:18px;margin-bottom:44px}
.avatar{flex:0 0 70px;height:70px;border-radius:50%;background:#c9ced3}
.review h4{font-size:15px;margin-bottom:2px}
.review .who{font-size:11px;margin-bottom:8px;display:block}
.review p{font-size:12px;margin-bottom:8px}
.converter{display:flex;gap:10px;align-items:center;margin-bottom:20px}
.converter .box{border:1px solid var(--line);height:36px;padding:8px 10px;font-size:12px;display:flex;justify-content:space-between;align-items:center}
.converter .result{background:var(--soft);font-weight:700;color:var(--ink);width:80px}
.center{text-align:center}

/* newsletter */
.newsletter{height:260px;background:var(--teal);text-align:center;padding-top:64px;color:#e5f6f4}
.newsletter h2{color:#fff;font-size:22px;letter-spacing:1px}
.newsletter p{font-size:12px;margin:6px 0 24px;font-style:italic}
.subscribe{display:flex;justify-content:center}
.subscribe .input{width:260px;height:40px;background:#fff;text-align:left;padding:10px 14px;color:#999;font-size:12px}
.subscribe .btn{border-radius:0;padding:13px 22px}

/* footer */
.footer{height:360px;background:var(--footer);color:#9aa1a8;padding-top:48px;font-size:12px}
.footer .wrap{display:grid;grid-template-columns:repeat(4,1fr);gap:40px}
.footer h4{color:#fff;font-size:13px;letter-spacing:1px;margin-bottom:18px}
.seal{width:70px;height:70px;border-radius:50%;background:#3d434a;margin-top:18px}
.post{display:flex;gap:12px;margin-bottom:16px}
.post .thumb{flex:0 0 56px;height:46px;background:linear-gradient(135deg,#b77b4c,#5d7b5a)}
.post b{color:#fff;display:block;font-weight:600}
.tweet{margin-bottom:14px}
.tweet b{color:#fff;font-weight:600}
.tweet a{color:var(--teal)}
.contact li{list-style:none;display:flex;gap:10px;align-items:center;margin-bottom:12px}
.contact .dot{width:22px;height:22px;border-radius:50%;background:#3d434a;display:flex;align-items:center;justify-content:center;flex:0 0 22px}
.bottombar{height:36px;background:#23272c;color:#7d848b;font-size:11px}
.bottombar .wrap{display:flex;justify-content:space-between;align-items:center;height:36px}
</style>
</head>
<body>

<div class="topbar"><div class="wrap">
  <div>+1 555 014 2210 &nbsp;&nbsp; hello@calderakey.example &nbsp;&nbsp; 8am - 6pm</div>
  <div class="social"><span></span><span></span><span></span><span></span><span></span></div>
</div></div>

<header class="header"><div class="wrap">
  <div class="brand"><i></i>Caldera Key</div>
  <nav class="nav"><a class="active">HOME</a><a>TOURS</a><a>NEWS</a><a>PAGES</a><a>SHOP</a><a>CONTACT US</a></nav>
</div></header>

<section class="hero" role="img" aria-label="Traveler with suitcase walking down a country road under a blue sky">
  <div class="arrow l"><svg width="12" height="12" viewBox="0 0 12 12"><path d="M8 1 3 6l5 5" stroke="#fff" stroke-width="2" fill="none"/></svg></div>
  <h1>TRAVEL WITH US &nbsp;&nbsp;&nbsp; FOR THE BEST DEAL</h1>
  <div class="arrow r"><svg width="12" height="12" viewBox="0 0 12 12"><path d="M4 1l5 5-5 5" stroke="#fff" stroke-width="2" fill="none"/></svg></div>
</section>

<section class="why"><div class="wrap">
  <div>
    <h2>WHY CHOOSE US?</h2>
    <div class="features">
      <div class="feature"><div class="ic"><svg width="18" height="18" viewBox="0 0 18 18"><circle cx="9" cy="9" r="7" stroke="#fff" stroke-width="2" fill="none"/></svg></div><div><h4>Diverse destinations</h4><p>Explore coast, highland and town trips chosen for every kind of traveler.</p></div></div>
      <div class="feature"><div class="ic"><svg width="18" height="18" viewBox="0 0 18 18"><path d="M3 9h12M9 3v12" stroke="#fff" stroke-width="2"/></svg></div><div><h4>Best prices</h4><p>Fair local rates with no hidden fees and clear options for every budget.</p></div></div>
      <div class="feature"><div class="ic"><svg width="18" height="18" viewBox="0 0 18 18"><path d="M2 14l5-7 4 5 2-3 3 5z" fill="#fff"/></svg></div><div><h4>Beautiful places</h4><p>Volcano views, waterfalls and coffee farms are waiting close to town.</p></div></div>
      <div class="feature"><div class="ic"><svg width="18" height="18" viewBox="0 0 18 18"><path d="M3 9l4 4 8-8" stroke="#fff" stroke-width="2" fill="none"/></svg></div><div><h4>Fast booking</h4><p>Reserve a tour in a few clicks and get your confirmation right away.</p></div></div>
      <div class="feature"><div class="ic"><svg width="18" height="18" viewBox="0 0 18 18"><path d="M4 3h3l1 4-2 1a9 9 0 0 0 4 4l1-2 4 1v3c-7 1-12-4-11-11z" fill="#fff"/></svg></div><div><h4>Instant help</h4><p>Our local team answers questions by phone or message every day.</p></div></div>
      <div class="feature"><div class="ic"><svg width="18" height="18" viewBox="0 0 18 18"><path d="M9 15S2 11 2 6a3.5 3.5 0 0 1 7-1 3.5 3.5 0 0 1 7 1c0 5-7 9-7 9z" fill="#fff"/></svg></div><div><h4>Emotional travel</h4><p>Trips built around stories, people and moments you will remember.</p></div></div>
    </div>
  </div>
  <aside class="search">
    <h3>Search Tours</h3>
    <small>Find your dream tour today</small>
    <div class="field">Keyword</div>
    <div class="field">Destination <span>▾</span></div>
    <div class="field">Tour Type <span>▾</span></div>
    <div class="field">Month <span>▾</span></div>
    <span class="btn btn-dark">FIND TOURS</span>
  </aside>
</div></section>

<section class="popular">
  <span class="script">Take a Look at Our</span>
  <h2 class="section-title">MOST POPULAR TOURS</h2>
  <div class="arrow l"><svg width="12" height="12" viewBox="0 0 12 12"><path d="M8 1 3 6l5 5" stroke="#fff" stroke-width="2" fill="none"/></svg></div>
  <div class="cards3">
    <article class="tour"><div class="photo" role="img" aria-label="Rafting group on white water" style="background:linear-gradient(160deg,#6da84f,#2f7fa6 60%,#dce9ee)"><span class="ribbon">HOT</span><span class="price"><s>$450</s>$199</span></div>
      <div class="body"><h3>Rafting</h3><p>Paddle the Chiriquí river rapids with trained guides and full safety gear.</p></div>
      <div class="meta"><span>10 Days</span><span class="stars">★★★★★</span></div></article>
    <article class="tour"><div class="photo" role="img" aria-label="Paraglider flying above green hills" style="background:linear-gradient(180deg,#74b3e6,#a8d1ef 50%,#6f9a4b)"><span class="price">$399</span></div>
      <div class="body"><h3>Paragliding</h3><p>Glide over the valley with a certified pilot and see the whole region.</p></div>
      <div class="meta"><span>10 Days</span><span class="stars">★★★★★</span></div></article>
    <article class="tour"><div class="photo" role="img" aria-label="Hot air balloon over a canyon" style="background:linear-gradient(180deg,#8fc3e8,#cfe1ea 55%,#b07b4c)"><span class="ribbon">SALE</span><span class="price"><s>$300</s>$249</span></div>
      <div class="body"><h3>Hot Air Ballooning</h3><p>Rise at sunrise over the highlands and enjoy a calm, quiet flight.</p></div>
      <div class="meta"><span>8 Hours</span><span class="stars">★★★★★</span></div></article>
  </div>
  <div class="arrow r"><svg width="12" height="12" viewBox="0 0 12 12"><path d="M4 1l5 5-5 5" stroke="#fff" stroke-width="2" fill="none"/></svg></div>
</section>

<section class="deals"><div class="wrap">
  <div class="head"><h2>DEALS AND DISCOUNTS</h2><span class="btn">VIEW MORE &#8250;</span></div>
  <p class="sub">Limited time offers on local tours, stays and activities across the highland region.</p>
  <div class="cards4">
    <article class="deal"><div class="photo" role="img" aria-label="Mountain lake in the Canadian Rockies" style="background:linear-gradient(180deg,#7db5dc,#4d8a5c 60%,#3a6b8a)"><span class="badge">$1,000<small>-20%</small></span></div>
      <div class="body"><h3>Canadian Rockies</h3><p>Seven days of alpine lakes, glaciers and mountain trails.</p></div>
      <div class="meta"><span>6 Days</span><span class="stars">★★★★★</span></div></article>
    <article class="deal"><div class="photo" role="img" aria-label="Lake shoreline with pines" style="background:linear-gradient(180deg,#7fb7e0,#3a7ba8 50%,#4e6f3c)"><span class="badge">$350<small>-15%</small></span></div>
      <div class="body"><h3>Lake Tahoe Adventure</h3><p>Kayak, hike and relax on the clear waters of the lake.</p></div>
      <div class="meta"><span>5 Days</span><span class="stars">★★★★★</span></div></article>
    <article class="deal"><div class="photo" role="img" aria-label="River cruise through tropical forest" style="background:linear-gradient(180deg,#a9cfe0,#5f8f44 55%,#3d5c2e)"><span class="badge">$1,400<small>-10%</small></span></div>
      <div class="body"><h3>Brivelle Cruise</h3><p>Sail deep into the rainforest with expert naturalists.</p></div>
      <div class="meta"><span>7 Days</span><span class="stars">★★★★★</span></div></article>
    <article class="deal"><div class="photo" role="img" aria-label="Waterfall in a jungle" style="background:linear-gradient(180deg,#5f9a4e,#cfe6e9 50%,#3b7a4a)"><span class="badge">$1,200<small>-25%</small></span></div>
      <div class="body"><h3>Discover Costa Rica</h3><p>Volcanoes, beaches and cloud forests in one easy trip.</p></div>
      <div class="meta"><span>8 Days</span><span class="stars">★★★★★</span></div></article>
  </div>
</div></section>

<section class="hot"><div class="wrap">
  <span class="script">Find a Tour by</span>
  <h2 class="section-title">HOT DESTINATIONS</h2>
  <div class="tiles">
    <div class="tile" role="img" aria-label="Colorful parrot in tropical forest" style="background:linear-gradient(135deg,#3b7d3a,#d8a23a 60%,#2f6fa0)"><span>Peru</span></div>
    <div class="tile" role="img" aria-label="Lake and mountains in Canada" style="background:linear-gradient(180deg,#8bbfe2,#3d7a9c 55%,#2f5a3a)"><span>Canada</span></div>
    <div class="tile" role="img" aria-label="Volcano above green valley" style="background:linear-gradient(180deg,#a9c9e2,#6b7e6b 50%,#3f7a38)"><span>Costa Rica</span></div>
    <div class="tile" role="img" aria-label="Large waterfall" style="background:linear-gradient(180deg,#7fb2d9,#dfeef3 50%,#4b8a4a)"><span>USA</span></div>
  </div>
</div></section>

<section class="types" role="img" aria-label="Dark mountain range background">
  <span class="script">Find a Tour by</span>
  <h2 class="section-title">TOUR TYPE</h2>
  <div class="arrow l"><svg width="12" height="12" viewBox="0 0 12 12"><path d="M8 1 3 6l5 5" stroke="#fff" stroke-width="2" fill="none"/></svg></div>
  <div class="type-row">
    <div class="type"><div class="ring"><svg width="44" height="44" viewBox="0 0 44 44" fill="none" stroke="#fff" stroke-width="2"><path d="M10 22a12 12 0 0 1 24 0z"/><path d="M12 22l8 12M32 22l-8 12M22 22v12"/><rect x="18" y="34" width="8" height="6"/></svg></div>AIR RIDES</div>
    <div class="type"><div class="ring"><svg width="44" height="44" viewBox="0 0 44 44" fill="none" stroke="#fff" stroke-width="2"><path d="M6 26h32l-5 8H11z"/><path d="M12 26v-8h18v8M18 18v-6h8v6"/></svg></div>CRUISES</div>
    <div class="type"><div class="ring"><svg width="44" height="44" viewBox="0 0 44 44" fill="none" stroke="#fff" stroke-width="2"><path d="M4 36l12-20 8 12 6-8 10 16z"/></svg></div>HIKING</div>
    <div class="type"><div class="ring"><svg width="44" height="44" viewBox="0 0 44 44" fill="none" stroke="#fff" stroke-width="2"><circle cx="22" cy="22" r="15"/><path d="M22 14l7 5-3 8h-8l-3-8z"/></svg></div>SPORTS</div>
    <div class="type"><div class="ring"><svg width="44" height="44" viewBox="0 0 44 44" fill="none" stroke="#fff" stroke-width="2"><ellipse cx="16" cy="16" rx="5" ry="8"/><ellipse cx="28" cy="26" rx="5" ry="8"/></svg></div>WALKING</div>
  </div>
  <div class="arrow r"><svg width="12" height="12" viewBox="0 0 12 12"><path d="M4 1l5 5-5 5" stroke="#fff" stroke-width="2" fill="none"/></svg></div>
</section>

<section class="insider"><div class="wrap">
  <div class="pick">
    <h2 class="col-h">OCTOBER INSIDER'S PICK</h2>
    <div class="photo" role="img" aria-label="Traveler standing on a cliff at sunset"></div>
    <div class="arrow l"><svg width="12" height="12" viewBox="0 0 12 12"><path d="M8 1 3 6l5 5" stroke="#fff" stroke-width="2" fill="none"/></svg></div>
    <div class="caption">
      <h3>Before You Go</h3>
      <p>Our local team shares what to pack, where to stay and the best times to visit the highlands this month.</p>
      <span class="btn">READ MORE &#8250;</span>
    </div>
    <div class="arrow r"><svg width="12" height="12" viewBox="0 0 12 12"><path d="M4 1l5 5-5 5" stroke="#fff" stroke-width="2" fill="none"/></svg></div>
  </div>
  <div class="side">
    <h2 class="col-h">TOUR REVIEWS</h2>
    <div class="review">
      <div class="avatar" role="img" aria-label="Reviewer portrait"></div>
      <div><h4>Canadian Rockies</h4><span class="who">Tessa R.</span>
      <p>The sightseeing and activities were better than we ever thought. Guides were friendly and helpful, and every day brought something new. We would book again.</p>
      <span class="stars">★★★★★</span></div>
    </div>
    <h2 class="col-h">CURRENCY CONVERTER</h2>
    <div class="converter">
      <div class="box" style="width:110px">U.S. Dollar <span>▾</span></div>
      <div class="box" style="width:60px">1</div>
      <span>TO</span>
      <div class="box" style="width:90px">Euro <span>▾</span></div>
      <div class="box result">0.70</div>
    </div>
    <div class="center"><span class="btn">CONVERT</span></div>
  </div>
</div></section>

<section class="newsletter">
  <h2>JOIN THE NEWSLETTER</h2>
  <p>To receive our best monthly deals</p>
  <div class="subscribe"><div class="input">Your Email</div><span class="btn btn-dark">SUBSCRIBE</span></div>
</section>

<footer class="footer"><div class="wrap">
  <div><h4>ABOUT US</h4><p>We are a small local company based in Caldera Key, offering tours, listings and stories for visitors and neighbors alike.</p><div class="seal"></div></div>
  <div><h4>FROM THE BLOG</h4>
    <div class="post"><div class="thumb" role="img" aria-label="Blog post photo"></div><div><b>Before You Go</b>June 22, 2015</div></div>
    <div class="post"><div class="thumb" role="img" aria-label="Blog post photo"></div><div><b>Costa Rica Parks</b>June 15, 2015</div></div>
  </div>
  <div><h4>LATEST TWEETS</h4>
    <div class="tweet"><b>@calderakey</b> New river tours are open for booking this week <a>ck.example/t3k</a></div>
    <div class="tweet"><b>@calderakey</b> Coffee farm visits are back with fresh tastings <a>ck.example/r8p</a></div>
  </div>
  <div><h4>CONTACT US</h4>
    <ul class="contact">
      <li><span class="dot"><svg width="10" height="12" viewBox="0 0 10 12"><path d="M5 12S0 7 0 4.5a5 5 0 0 1 10 0C10 7 5 12 5 12z" fill="#9aa1a8"/></svg></span>42 Harbor Lane, Caldera Key</li>
      <li><span class="dot"><svg width="10" height="10" viewBox="0 0 10 10"><path d="M1 1h3l1 2-1.5 1a6 6 0 0 0 2.5 2.5L7 5l2 1v3C4 9 1 6 1 1z" fill="#9aa1a8"/></svg></span>+1 555 014 2210</li>
      <li><span class="dot"><svg width="10" height="8" viewBox="0 0 10 8"><rect x=".5" y=".5" width="9" height="7" fill="none" stroke="#9aa1a8"/><path d="M.5.5l4.5 4 4.5-4" fill="none" stroke="#9aa1a8"/></svg></span>hello@calderakey.example</li>
      <li><span class="dot"><svg width="10" height="10" viewBox="0 0 10 10"><circle cx="5" cy="5" r="4" fill="none" stroke="#9aa1a8"/></svg></span>Caldera Key</li>
    </ul>
  </div>
</div></footer>

<div class="bottombar"><div class="wrap">
  <span>© Caldera Key 2015. All rights reserved.</span>
  <span>Terms &amp; Conditions &nbsp;&nbsp; Licenses &nbsp;&nbsp; Privacy Policy</span>
</div></div>

</body>
</html>
```